Project Overview:
We are looking to create a website for a monthly subscription IPTV service in WordPress. The website should provide a seamless user experience for customers to sign up for the service and manage their account information. We need the following pages: Home Page, Product Page, Sign-Up Page, and Account Information Page.

Home Page:
The Home Page design should be simple and clean, with a dark theme and minimalistic design elements. We would like to include graphics of popular movie shows displayed on multiple devices. The page should highlight the key benefits and features of our service and provide a clear call-to-action for visitors to sign up.

Product Page:
The Product Page should provide detailed information about our subscription tiers and pricing plans. It should highlight the key features of each plan and provide a clear comparison between them. The page should also include a call-to-action button for visitors to sign up.

Sign-Up Page:
The Sign-Up Page is the conversion page where members will sign up for the service. It should collect the following information: Name, Phone Number, Email, Password, and Payment Information. The design should be simple, intuitive, and easy to use. It should highlight the benefits of our service and provide a clear call-to-action for visitors to sign up.

Account Information Page:
The Account Information Page should allow members to view and manage their account details. It should include the following information: Profile Image, Contact Details, Password Management, Payment Information Management, and Membership Expiration Date. The design should be user-friendly, intuitive, and easy to navigate.

Goals: The primary goal of the website is to provide an easy-to-use portal for customers to sign up for the service and manage their account information. The website should be user-friendly and visually appealing to attract potential customers.

Scope: The scope of the project includes designing a home page, a sign-up page, an account information page, and a payment information page. The website should be designed to be responsive and accessible on desktop and mobile devices.

Design Preferences: The design should be clean, modern, and visually appealing. The use of a color palette that is consistent with the brand identity is recommended. The website should be easy to navigate and provide a clear call-to-action for users to sign up for the service.

FYI: The subscription service I am designing a website for is related to an IPTV service. IPTV stands for Internet Protocol Television, which is a digital television broadcasting protocol that uses the internet to deliver TV programs and videos to viewers. The website will allow customers to sign up for the IPTV service and access their account information such as user name and password, membership tier, name, and payment details. Please let me know if you have any further questions, and I would be happy to provide more details. Thank you!

Dear Designers,

Thank you for your participation in our project. After reviewing the designs received so far, we have decided to update the brief to better reflect our needs and preferences. We apologize for any confusion this may cause, but we believe that these changes will result in better design submissions and a more successful project overall.

The updated brief is as follows:

We are looking to create a website for WordPress.

Also, here is the updated Brief.

Project Title: WordPress Website Design for Monthly Subscription IPTV Service

Project Overview:
We are looking to create a website for a monthly subscription IPTV service. The website should provide a seamless user experience for customers to sign up for the service and manage their account information. We need the following pages: Home Page, Product Page, Sign-Up Page, and Account Information Page.

Home Page:

Product Page:

Sign-Up Page:

Account Information Page:

Design Preferences:
We prefer a dark theme with minimalistic design elements and hits of our logo colors. The website should be easy to use and navigate, with clear calls-to-action and simple, intuitive forms. The design should be optimized for mobile devices and load quickly.

We hope that these updates provide you with a clearer understanding of our requirements and preferences. Please let us know if you have any questions or concerns. We look forward to seeing your revised designs.

Thank you again for your participation.
We will guarantee this project as soon as we see something we like that meets the updated requirements.

The website's target audience is individuals who are interested in subscribing to the monthly service.

4 page

• One item for sale and a client profile section.

```html
<!DOCTYPE html>
<html lang="en">
<head>
<meta charset="utf-8">
<title>Streamora – Monthly Streaming Subscription</title>
<link rel="stylesheet" href="https://fonts.googleapis.com/css2?family=Open+Sans:wght@600;700;800&family=Lato:wght@400;700&family=Arimo:wght@700&display=swap">
<style>
:root{
  --red:#ff0000;
  --black:#000;
  --panel:#1a1a1a;
  --card:#161616;
  --white:#fff;
  --grey:#9a9a9a;
  --line:#5a5a5a;
}
*{box-sizing:border-box;margin:0;padding:0}
html,body{width:1200px;height:3578px;overflow:hidden;background:var(--black)}
body{position:relative;font-family:'Lato',sans-serif;color:var(--white)}
.abs{position:absolute}
.brand{font-family:'Open Sans',sans-serif;font-weight:800;color:var(--white);letter-spacing:1px;display:flex;align-items:center;gap:12px}
.brand-dot{background:var(--red);border-radius:50%}
/* header */
.header{left:0;top:0;width:1200px;height:129px;background:var(--black)}
.call{left:606px;top:44px;display:flex;align-items:center;gap:14px}
.call-label{font-family:'Open Sans',sans-serif;font-weight:700;font-size:16px}
.call-number{font-family:'Open Sans',sans-serif;font-weight:700;font-size:21px}
.social{left:852px;top:61px;display:flex;gap:8px}
.social span{width:27px;height:27px;border-radius:50%;display:block}
.lang{left:981px;top:66px;font-family:'Open Sans',sans-serif;font-weight:700;font-size:14px;display:flex;align-items:center;gap:6px}
.lang-dot{width:28px;height:28px;border-radius:50%;background:linear-gradient(180deg,#c8102e 0 50%,#f4f4f4 50% 100%);margin-left:8px}
.nav{left:0;top:129px;width:1200px;height:60px;background:var(--red)}
.nav a{position:absolute;top:0;height:60px;line-height:60px;font-family:'Open Sans',sans-serif;font-weight:700;font-size:14px;color:var(--white);text-decoration:none}
.nav a.active{background:var(--black);left:382px;width:67px;text-align:center}
/* hero */
.hero{left:0;top:189px;width:1200px;height:700px;background:linear-gradient(90deg,#5a3a30 0%,#2b2c38 30%,#1c2740 50%,#3a3530 75%,#6a5a48 100%)}
.hero-shade{left:254px;top:507px;width:691px;height:250px;background:rgba(0,0,0,.35)}
.hero-title{left:0;top:540px;width:1200px;text-align:center;font-family:'Open Sans',sans-serif;font-weight:700;font-size:62px}
.hero-sub{left:0;top:620px;width:1200px;text-align:center;font-family:'Open Sans',sans-serif;font-weight:700;font-size:21px}
.btn{display:block;background:var(--red);color:var(--white);border-radius:24px;text-align:center;font-family:'Open Sans',sans-serif;font-weight:700;font-size:14px;text-decoration:none}
.circle-arrow{width:44px;height:44px;border-radius:50%;background:var(--white);display:flex;align-items:center;justify-content:center}
.section-title{left:0;width:1200px;text-align:center;font-family:'Open Sans',sans-serif;font-weight:700}
/* benefits */
.benefit{width:310px;height:310px}
.benefit .shape{position:absolute;left:45px;top:45px;width:220px;height:220px;background:var(--panel);border-radius:48px;transform:rotate(45deg)}
.benefit .icon{position:absolute;left:119px;top:52px}
.benefit p{position:absolute;left:0;top:138px;width:310px;text-align:center;font-family:'Arimo',sans-serif;font-weight:700;font-size:19px;line-height:26px}
.benefit .go{position:absolute;left:135px;top:242px;width:40px;height:40px}
.go .sq{position:absolute;inset:0;background:var(--red);border-radius:8px;transform:rotate(45deg)}
.go svg{position:relative}
/* popular */
.screen{background:linear-gradient(135deg,#1b1f2a 0%,#3a2a22 45%,#b4501a 75%,#20160f 100%)}
/* features */
.feature{top:2547px;width:227px;height:156px;background:var(--card)}
.feature svg{position:absolute;left:80px;top:22px}
.feature p{position:absolute;left:0;top:108px;width:227px;text-align:center;font-family:'Arimo',sans-serif;font-weight:700;font-size:18px}
/* newsletter */
.field{top:2895px;height:37px;border-bottom:1px solid var(--line);font-size:13px;color:var(--grey);padding:6px 8px}
/* footer */
.footer{left:0;top:3133px;width:1200px;height:445px;background:#070707}
.foot-text{font-size:14px;line-height:26px;color:#e0e0e0}
.foot-head{font-family:'Lato',sans-serif;font-weight:700;font-size:19px;top:3285px}
.foot-head::after{content:"";display:block;width:36px;height:2px;background:var(--white);margin-top:8px}
.foot-list{top:3338px;list-style:none;font-size:14px;line-height:26px;color:#e0e0e0}
.foot-list li::before{content:"»";margin-right:10px}
.contact{left:886px;display:flex;gap:14px;font-size:14px;line-height:26px;color:#e0e0e0}
.contact i{width:26px;height:26px;background:var(--red);flex:none;display:flex;align-items:center;justify-content:center;margin-top:2px}
.rule{left:111px;top:3500px;width:978px;height:1px;background:#333}
.copy{left:0;top:3524px;width:1200px;text-align:center;font-size:14px}
</style>
</head>
<body>

<header class="abs header">
  <div class="abs brand" style="left:121px;top:28px;font-size:54px"><span class="brand-dot" style="width:22px;height:22px"></span>STREAMORA</div>
  <div class="abs call">
    <svg width="48" height="48" viewBox="0 0 48 48"><circle cx="24" cy="24" r="21" fill="none" stroke="#ff0000" stroke-width="3"/><path d="M16 14c2-1 4 3 4 5s-2 2-1 4 4 5 6 6 2-1 4-1 6 2 5 4-3 4-6 3-9-5-12-9-3-10 0-12z" fill="#ff0000"/></svg>
    <div><div class="call-label">Call us Today :</div><div class="call-number">+1 888 888 8888</div></div>
  </div>
  <div class="abs social"><span style="background:#3b5dc0"></span><span style="background:#2b9de0"></span><span style="background:#e64033"></span></div>
  <div class="abs lang">Eng <svg width="10" height="8" viewBox="0 0 10 8"><path d="M1 2l4 4 4-4" stroke="#fff" stroke-width="1.5" fill="none"/></svg><span class="lang-dot"></span></div>
</header>

<nav class="abs nav">
  <a class="active" href="#">HOME</a>
  <a href="#" style="left:462px">PRODUCT</a>
  <a href="#" style="left:553px">SIGN-UP</a>
  <a href="#" style="left:633px">ACCOUNT INFORMATION</a>
</nav>

<section class="abs hero" role="img" aria-label="Friends relaxing together on a sofa in a city apartment at night"></section>
<div class="abs hero-shade"></div>
<h1 class="abs hero-title">STREAMORA</h1>
<p class="abs hero-sub">SUBSCRIPTION-BASED WEBSITE FOR A MONTHLY SERVICE</p>
<a class="abs btn" href="#" style="left:526px;top:667px;width:148px;height:44px;line-height:44px">SIGNUP</a>
<div class="abs circle-arrow" style="left:67px;top:479px"><svg width="12" height="12" viewBox="0 0 12 12"><path d="M8 1L3 6l5 5" stroke="#e0a000" stroke-width="2" fill="none"/></svg></div>
<div class="abs circle-arrow" style="left:1089px;top:479px"><svg width="12" height="12" viewBox="0 0 12 12"><path d="M4 1l5 5-5 5" stroke="#e0a000" stroke-width="2" fill="none"/></svg></div>
<svg class="abs" style="left:0;top:780px" width="1200" height="110" viewBox="0 0 1200 110">
  <path d="M0 110L0 109Q600 10 1200 109L1200 110Z" fill="#000"/>
  <path d="M111 86Q600 -20 1089 86Q600 0 111 86Z" fill="#ff0000"/>
  <path d="M120 86Q600 5 1080 86L1200 110L0 110Z" fill="#000"/>
</svg>

<h2 class="abs section-title" style="top:920px;font-size:60px">KEY BENEFITS</h2>

<div class="abs benefit" style="left:113px;top:1021px">
  <div class="shape"></div>
  <svg class="icon" width="72" height="72" viewBox="0 0 80 80" fill="none" stroke="#fff" stroke-width="2.5"><rect x="4" y="8" width="46" height="32"/><path d="M22 16v16l12-8z"/><path d="M12 40l4 30h16l4-30M20 44v22M28 44v22"/><rect x="44" y="20" width="32" height="24"/><path d="M44 14l30-8 2 8-30 8z"/></svg>
  <p>Lorem ipsum dol<br>or sit amet</p>
  <div class="go"><div class="sq"></div><svg width="40" height="40" viewBox="0 0 40 40"><path d="M13 20h12M20 14l6 6-6 6" stroke="#fff" stroke-width="3" fill="none"/></svg></div>
</div>
<div class="abs benefit" style="left:446px;top:1021px">
  <div class="shape"></div>
  <svg class="icon" width="72" height="72" viewBox="0 0 80 80" fill="none" stroke="#fff" stroke-width="2.5"><rect x="8" y="6" width="64" height="62" rx="4"/><path d="M34 14v18l14-9z"/><circle cx="24" cy="46" r="5"/><circle cx="40" cy="46" r="5"/><circle cx="56" cy="46" r="5"/><path d="M16 64c0-6 16-6 16 0M32 64c0-6 16-6 16 0M48 64c0-6 16-6 16 0"/></svg>
  <p>Lorem ipsum dol<br>or sit amet</p>
  <div class="go"><div class="sq"></div><svg width="40" height="40" viewBox="0 0 40 40"><path d="M13 20h12M20 14l6 6-6 6" stroke="#fff" stroke-width="3" fill="none"/></svg></div>
</div>
<div class="abs benefit" style="left:780px;top:1021px">
  <div class="shape"></div>
  <svg class="icon" width="72" height="72" viewBox="0 0 80 80" fill="none" stroke="#fff" stroke-width="2.5"><rect x="10" y="30" width="60" height="38"/><path d="M8 20l58-14 3 12-58 14z"/><path d="M22 42h36M22 52h36M22 60h24"/></svg>
  <p>Lorem ipsum dol<br>or sit amet</p>
  <div class="go"><div class="sq"></div><svg width="40" height="40" viewBox="0 0 40 40"><path d="M13 20h12M20 14l6 6-6 6" stroke="#fff" stroke-width="3" fill="none"/></svg></div>
</div>
<div class="abs benefit" style="left:280px;top:1244px">
  <div class="shape"></div>
  <svg class="icon" width="72" height="72" viewBox="0 0 80 80" fill="none" stroke="#fff" stroke-width="2.5"><rect x="12" y="4" width="56" height="38"/><circle cx="40" cy="23" r="10"/><path d="M37 18v10l8-5z"/><path d="M6 52h68v14H6zM14 52v-6h20v6M46 52v-6h20v6M10 66v6M70 66v6"/></svg>
  <p>Lorem ipsum dol<br>or sit amet</p>
  <div class="go"><div class="sq"></div><svg width="40" height="40" viewBox="0 0 40 40"><path d="M13 20h12M20 14l6 6-6 6" stroke="#fff" stroke-width="3" fill="none"/></svg></div>
</div>
<div class="abs benefit" style="left:613px;top:1244px">
  <div class="shape"></div>
  <svg class="icon" width="72" height="72" viewBox="0 0 80 80" fill="none" stroke="#fff" stroke-width="2.5"><circle cx="40" cy="22" r="11"/><path d="M26 70V48c0-8 28-8 28 0v22"/><circle cx="16" cy="36" r="8"/><path d="M4 70V56c0-6 20-6 20 0"/><circle cx="64" cy="36" r="8"/><path d="M56 56c0-6 20-6 20 0v14"/></svg>
  <p>Lorem ipsum dol<br>or sit amet</p>
  <div class="go"><div class="sq"></div><svg width="40" height="40" viewBox="0 0 40 40"><path d="M13 20h12M20 14l6 6-6 6" stroke="#fff" stroke-width="3" fill="none"/></svg></div>
</div>

<svg class="abs" style="left:0;top:1681px" width="1200" height="688" viewBox="0 0 1200 688"><path d="M0 76Q600 -76 1200 76L1200 688L0 688Z" fill="#ff0000"/></svg>
<h2 class="abs section-title" style="top:1800px;font-size:37px">POPULAR MOVIE SHOWS</h2>

<div class="abs" style="left:139px;top:1997px;width:257px;height:167px;background:#d9d9d9;border-radius:6px;padding:10px">
  <div class="screen" style="width:100%;height:100%" role="img" aria-label="Action movie still shown on a tablet"></div>
</div>
<div class="abs" style="left:443px;top:1921px;width:463px;height:304px;background:#e6e6e6;border-radius:12px 12px 0 0;padding:20px 22px 20px">
  <div class="screen" style="width:100%;height:100%" role="img" aria-label="Action movie still shown on a laptop"></div>
</div>
<div class="abs" style="left:392px;top:2225px;width:566px;height:14px;background:#eeeeee;border-radius:0 0 60px 60px"></div>
<div class="abs" style="left:965px;top:1977px;width:95px;height:190px;background:#e6e6e6;border-radius:12px;padding:10px 6px">
  <div class="screen" style="width:100%;height:100%;border-radius:6px" role="img" aria-label="Action movie still shown on a phone"></div>
</div>
<div class="abs circle-arrow" style="left:39px;top:2064px;width:34px;height:34px"><svg width="10" height="12" viewBox="0 0 10 12"><path d="M7 1L2 6l5 5" stroke="#000" stroke-width="2" fill="none"/></svg></div>
<div class="abs circle-arrow" style="left:1127px;top:2064px;width:34px;height:34px"><svg width="10" height="12" viewBox="0 0 10 12"><path d="M3 1l5 5-5 5" stroke="#000" stroke-width="2" fill="none"/></svg></div>

<h2 class="abs section-title" style="top:2462px;font-size:37px">FEATURES OF OUR SERVICE</h2>
<div class="abs feature" style="left:111px"><svg width="68" height="68" viewBox="0 0 68 68" fill="none" stroke="#fff" stroke-width="2.5"><circle cx="34" cy="32" r="28"/><circle cx="34" cy="32" r="5"/><circle cx="34" cy="14" r="7"/><circle cx="34" cy="50" r="7"/><circle cx="16" cy="32" r="7"/><circle cx="52" cy="32" r="7"/><path d="M12 58h44v8H12z"/></svg><p>Nemo enim ipsam</p></div>
<div class="abs feature" style="left:361px"><svg width="68" height="68" viewBox="0 0 68 68" fill="none" stroke="#fff" stroke-width="2.5"><rect x="4" y="4" width="60" height="48"/><circle cx="38" cy="20" r="8"/><path d="M36 16v8l6-4z"/><path d="M6 32h14l-2 34H8z"/><path d="M30 66V46h30v20"/></svg><p>Nemo enim ipsam</p></div>
<div class="abs feature" style="left:611px"><svg width="68" height="68" viewBox="0 0 68 68" fill="none" stroke="#fff" stroke-width="2.5"><circle cx="34" cy="18" r="12"/><path d="M20 66V44c0-10 28-10 28 0v22"/><circle cx="12" cy="34" r="7"/><path d="M2 66V52c0-6 18-6 18 0"/><circle cx="56" cy="34" r="7"/><path d="M48 52c0-6 18-6 18 0v14"/></svg><p>Nemo enim ipsam</p></div>
<div class="abs feature" style="left:861px"><svg width="68" height="68" viewBox="0 0 68 68" fill="none" stroke="#fff" stroke-width="2.5"><path d="M10 4l8 8-4 4-8-8M16 14l40 40M50 50l12 12-6 6-12-12"/><path d="M58 8a12 12 0 0 0-14 16L8 58l4 4 34-34a12 12 0 0 0 16-14l-8 6-6-2-2-6z"/></svg><p>Nemo enim ipsam</p></div>

<h2 class="abs section-title" style="top:2820px;font-size:37px">SIGNUP TO OUR NEWSLETTER</h2>
<div class="abs field" style="left:219px;width:371px">Name</div>
<div class="abs field" style="left:611px;width:368px">Email address</div>
<a class="abs btn" href="#" style="left:526px;top:2977px;width:148px;height:44px;line-height:44px">SIGNUP</a>

<footer class="abs footer"></footer>
<svg class="abs" style="left:0;top:3125px" width="1200" height="90" viewBox="0 0 1200 90"><path d="M0 0H1200V80Q600 -10 0 80Z" fill="#000"/><path d="M111 80Q600 -40 1089 80Q600 10 111 80Z" fill="#ff0000"/></svg>
<div class="abs brand" style="left:111px;top:3278px;font-size:28px;gap:8px"><span class="brand-dot" style="width:12px;height:12px"></span>STREAMORA</div>
<p class="abs foot-text" style="left:111px;top:3326px;width:250px">Lorem ipsum dolor sit amet, consectetur adipiscing elit, sed do eiusmod tempor incididunt ut labore Lorem ipsum dolor sit amet, consectetur adipiscing elit</p>
<h3 class="abs foot-head" style="left:453px">Services</h3>
<ul class="abs foot-list" style="left:453px"><li>Lorem ipsum</li><li>Dolor sit amet,</li><li>Consectetur</li><li>Adipiscing</li><li>Dolor sit amet,</li></ul>
<h3 class="abs foot-head" style="left:658px">Quick Links</h3>
<ul class="abs foot-list" style="left:658px"><li>Home</li><li>About Us</li><li>Blogs</li><li>Team</li><li>Contact us</li></ul>
<h3 class="abs foot-head" style="left:886px">Contact us</h3>
<div class="abs contact" style="top:3330px;width:210px"><i><svg width="12" height="14" viewBox="0 0 12 14"><path d="M6 13S1 8 1 5a5 5 0 0 1 10 0c0 3-5 8-5 8z" fill="#fff"/><circle cx="6" cy="5" r="2" fill="#ff0000"/></svg></i><span>123,Lorem ipsum dolor sit consectetur</span></div>
<div class="abs contact" style="top:3392px"><i><svg width="12" height="12" viewBox="0 0 12 12"><path d="M2 1c1 0 2 2 2 3s-1 1 0 2 2 2 3 2 1-1 2 0 2 1 2 2-1 2-3 1S2 7 1 5 1 1 2 1z" fill="#fff"/></svg></i><span>+1 888 888 8888</span></div>
<div class="abs contact" style="top:3443px"><i><svg width="14" height="10" viewBox="0 0 14 10"><rect width="14" height="10" fill="#fff"/><path d="M0 0l7 5 7-5" stroke="#ff0000" fill="none"/></svg></i><span>info@companyname.com</span></div>
<div class="abs rule"></div>
<p class="abs copy">© Copyright @2023 Company name | All Rights Reserved</p>

</body>
</html>
```